Business card design for a dynamic IT consulting company

We need a business card design for a young firm, specialized in the Telecommunications/Consulting industry. The name of the company is Quindor and Partners Business Consulting Ltd. (Short name: Quindor and Partnes)
Quindor = solve read reverse, so we aim to be uncomplicated and solution-oriented. The small pipe in our logo is also related to the word solve. So we need a new business card design, which is simple, eye catching and something non traditional (I would probably prefer a square shaped design rather than a rectangle, but open for suggestions). Attached our logo.

Target Market(s)

Usually our customers are Tier1 Telecoms providers (Q-Netra, Palorix, etc) and their executives.

Industry/Entity Type

Business

Contact Information for Business Card

Name: Bence Tolnavari
Email: b.tolnavari@quindor.hu
Web: www.quindor.hu
Mobile: +36 30 518 2769
Title: Managing Director

Optional:
Company name: Quindor and Partners Ltd.
Address: 1087 Budapest, Tolvenka str. 28/C, Hungary

Font styles to use
Other font styles liked:
• helveticaneue_medium, Prime Regular are used now.

Colors

Designer to choose colors to be used in the design.

Requirements
Must have
• I would like to have a 2 sided design.
Nice to have
• I thought if we make the logo a bit bigger (without the company name), that could go to the back with the company name below. I though, if the pipe in the logo is somehow touchable on the business card, would be nice and unique.

```html
<!DOCTYPE html>
<html lang="en">
<head>
<meta charset="utf-8">
<title>Quindor &amp; Partners – Business Card</title>
<link rel="stylesheet" href="https://fonts.googleapis.com/css2?family=Open+Sans:wght@400;600;700&display=swap">
<style>
  :root {
    --cyan: #0a9bdc;
    --magenta: #b52e93;
    --graphite: #5f5f60;
    --paper: #ffffff;
    --stage: #ecebe8;
    --ink-light: #ffffff;
  }
  * { margin: 0; padding: 0; box-sizing: border-box; }
  html, body {
    width: 1200px; height: 900px; overflow: hidden;
    background: var(--stage);
    font-family: "Open Sans", Arial, sans-serif;
  }
  .canvas { position: relative; width: 1200px; height: 900px; }

  .card {
    position: absolute;
    width: 620px; height: 354px;
    overflow: hidden;
    box-shadow: 0 6px 18px rgba(0,0,0,0.18);
  }

  /* Back side */
  .card-back {
    left: 90px; top: 70px;
    background: var(--cyan);
    display: flex; align-items: center; justify-content: center;
  }
  .back-brand {
    display: flex; align-items: center; gap: 14px;
    color: var(--ink-light);
    font-weight: 600; font-size: 44px; letter-spacing: 1px;
  }
  .back-brand .mark-square {
    width: 22px; height: 22px; background: var(--ink-light);
  }

  /* Front side */
  .card-front {
    left: 490px; top: 476px;
    background: var(--paper);
  }
  .front-header {
    position: absolute; left: 0; top: 0; width: 100%; height: 156px;
    display: flex; align-items: center; justify-content: center;
  }
  .front-brand {
    display: flex; align-items: center; gap: 14px;
    color: var(--graphite);
    font-weight: 400; font-size: 40px; line-height: 1;
  }
  .front-brand .mark-square {
    width: 20px; height: 20px; background: var(--magenta);
  }

  .contact-band {
    position: absolute; left: 0; top: 156px; width: 100%; height: 128px;
    background: var(--cyan);
    color: var(--ink-light);
  }
  .contact-list {
    position: absolute; right: 318px; top: 22px;
    list-style: none;
    display: flex; flex-direction: column; align-items: flex-end; gap: 5px;
    font-size: 14.5px;
  }
  .contact-list li { display: flex; align-items: center; gap: 8px; white-space: nowrap; }
  .contact-list svg { width: 13px; height: 13px; fill: var(--ink-light); flex: none; }
  .person {
    position: absolute; left: 330px; top: 16px;
  }
  .person-name { font-weight: 700; font-size: 17px; }
  .person-title { font-size: 12.5px; margin-top: 2px; }

  .address-band {
    position: absolute; left: 0; top: 284px; width: 100%; height: 70px;
    background: var(--magenta);
    color: var(--ink-light);
    display: flex; align-items: center; justify-content: center;
    font-size: 17px;
  }
</style>
</head>
<body>
<main class="canvas">
  <section class="card card-back" aria-label="Business card back">
    <div class="back-brand">
      <span class="mark-square"></span>
      <span>Quindor</span>
    </div>
  </section>

  <section class="card card-front" aria-label="Business card front">
    <header class="front-header">
      <div class="front-brand">
        <span class="mark-square"></span>
        <span>Quindor &amp; Partners</span>
      </div>
    </header>

    <div class="contact-band">
      <ul class="contact-list">
        <li>+36 30 518 2769
          <svg viewBox="0 0 24 24" aria-hidden="true"><path d="M6.6 10.8a15.1 15.1 0 0 0 6.6 6.6l2.2-2.2c.3-.3.7-.4 1-.2 1.1.4 2.3.6 3.6.6.6 0 1 .4 1 1V20c0 .6-.4 1-1 1A17 17 0 0 1 3 4c0-.6.4-1 1-1h3.5c.6 0 1 .4 1 1 0 1.3.2 2.5.6 3.6.1.3 0 .7-.2 1z"/></svg>
        </li>
        <li>b.tolnavari@quindor.hu
          <svg viewBox="0 0 24 24" aria-hidden="true"><path d="M2 5h20v14H2z"/><path d="M3 6.5l9 6 9-6" fill="none" stroke="#0a9bdc" stroke-width="2"/></svg>
        </li>
        <li>www.quindor.hu
          <svg viewBox="0 0 24 24" aria-hidden="true"><circle cx="12" cy="12" r="10"/><path d="M2 12h20M12 2c3 3 3 17 0 20M12 2c-3 3-3 17 0 20" fill="none" stroke="#0a9bdc" stroke-width="1.6"/></svg>
        </li>
      </ul>
      <div class="person">
        <p class="person-name">Bence Tolnavari</p>
        <p class="person-title">Managing Director</p>
      </div>
    </div>

    <footer class="address-band">1087 Budapest, Tolvenka str. 28/C, Hungary</footer>
  </section>
</main>
</body>
</html>
```